Audio/ Video Packaging Design for a Technology company.

We need a packaging design for a bag that is 7" wide and 10" high. The design will be for a new line of audio/video products. We would like to see designs that represent a superior quality product that provides a pure connection. We want the equivalent of a nice retail bag that you would find in a store like Tallow Mart. It should be a maximum of three colors. We really want something sharp, professional and eye catching, not whimsical or cartoonish. I've included a couple of examples below. I don't really like the designs of the bags, but I want you to see examples of what I'm looking for.

The company logo, which is uploaded, should be on the design. The words "audio and video products" should be either underneath the logo or to the side. Also, somewhere on the bag, we would like the words "For a Pure Connection"

The winner of this contest will likely get the opportunity for additional work as we have more products ready to launch.

Target Market(s)

resellers, consumers - men 25-60

Industry/Entity Type

It Company

Requirements
Must have
• It should be a maximum of three colors. We really want something sharp, professional and eye catching, not whimsical or cartoonish
Nice to have
• Eye-catching design. Utilize the entire bag but don't make it too busy.
Should not have
• Whimsical, cartoonish

```html
<!DOCTYPE html>
<html lang="en">
<head>
<meta charset="utf-8">
<title>Veritor Power Cable Package</title>
<link rel="stylesheet" href="https://fonts.googleapis.com/css2?family=Montserrat:wght@500;600;700&family=Nunito:wght@600&display=swap">
<style>
  :root {
    --backdrop: #8c8c8c;
    --card-white: #ffffff;
    --ink-dark: #2b2d33;
    --panel-dark: #3a3a3c;
    --brand-blue: #2a6fdb;
    --accent-cyan: #3fd0f4;
    --window-light: #e6e6e6;
    --window-mid: #a9a9a9;
    --muted: #8a8a8a;
  }
  html, body {
    margin: 0;
    padding: 0;
    width: 1200px;
    height: 960px;
    overflow: hidden;
    background: var(--backdrop);
  }
  .package {
    position: absolute;
    left: 310px;
    top: 50px;
    width: 580px;
    height: 860px;
    display: block;
  }
  .brand-name { font-family: "Montserrat", sans-serif; font-weight: 500; fill: var(--ink-dark); }
  .brand-tagline { font-family: "Nunito", sans-serif; font-weight: 600; fill: var(--brand-blue); letter-spacing: 1.5px; }
  .product-type { font-family: "Montserrat", sans-serif; font-weight: 700; fill: var(--accent-cyan); }
  .power-label { font-family: "Montserrat", sans-serif; font-weight: 600; fill: var(--panel-dark); }
  .voltage { font-family: "Montserrat", sans-serif; font-weight: 500; fill: var(--accent-cyan); }
  .slogan { font-family: "Montserrat", sans-serif; font-weight: 500; fill: var(--card-white); }
  .origin { font-family: "Montserrat", sans-serif; font-weight: 500; fill: var(--muted); letter-spacing: 1px; }
</style>
</head>
<body>
<svg class="package" viewBox="0 0 600 890" xmlns="http://www.w3.org/2000/svg" aria-label="Veritor power cable retail package">
  <defs>
    <clipPath id="card-shape">
      <rect x="0" y="0" width="600" height="890" rx="40" ry="40"/>
    </clipPath>
    <linearGradient id="window-fill" x1="0" y1="0" x2="1" y2="1">
      <stop offset="0" stop-color="var(--window-light)"/>
      <stop offset="0.55" stop-color="var(--window-mid)"/>
      <stop offset="1" stop-color="var(--window-light)"/>
    </linearGradient>
  </defs>

  <g clip-path="url(#card-shape)">
    <rect class="card-base" x="0" y="0" width="600" height="890" fill="var(--card-white)"/>

    <!-- hang hole -->
    <path class="hang-hole" d="M253 35 Q255 18 300 18 Q345 18 347 35 L350 35 Q370 35 370 52 Q370 68 350 68 L250 68 Q230 68 230 52 Q230 35 250 35 Z" fill="var(--panel-dark)"/>

    <!-- brand lockup -->
    <rect class="brand-mark" x="146" y="165" width="32" height="32" fill="var(--brand-blue)"/>
    <text class="brand-name" x="192" y="200" font-size="46">VERITOR</text>
    <text class="brand-tagline" x="300" y="236" font-size="20" text-anchor="middle">audio and video products</text>

    <!-- product window -->
    <rect class="product-window" x="103" y="277" width="392" height="450" rx="30" ry="30" fill="url(#window-fill)" stroke="#d0d0d0" stroke-width="1" role="img" aria-label="Clear window showing the coiled USB cable inside"/>

    <!-- chevron bands -->
    <polygon class="band-blue" points="0,378 358,650 600,292 600,890 0,890" fill="var(--brand-blue)"/>
    <polygon class="band-white" points="0,398 360,670 600,316 600,890 0,890" fill="var(--card-white)"/>
    <polygon class="panel-dark" points="0,414 362,690 600,336 600,890 0,890" fill="var(--panel-dark)"/>

    <!-- product labels -->
    <rect class="power-tag" x="32" y="672" width="34" height="130" fill="var(--accent-cyan)"/>
    <text class="power-label" transform="translate(59 796) rotate(-90)" font-size="26">POWER</text>
    <text class="voltage" transform="translate(94 802) rotate(-90)" font-size="22">110V ~300V</text>
    <text class="product-type" x="108" y="800" font-size="84" textLength="305" lengthAdjust="spacingAndGlyphs">CABLE</text>
    <line class="label-rule" x1="72" y1="808" x2="412" y2="808" stroke="var(--accent-cyan)" stroke-width="1.5"/>
    <text class="slogan" x="262" y="843" font-size="22" text-anchor="middle">“For a Pure Connection”</text>
    <text class="origin" transform="translate(586 832) rotate(-90)" font-size="10">MADE IN CHINA</text>
  </g>
</svg>
</body>
</html>
```